Theme and starter template for small business powerpoint deck

We are starting a technology consulting company and would like to have a powerpoint/google slide theme and initial template. We are more concerned with the theme/colors at this point. Initial template can be pretty simple. We would want a cover slide, agenda slide, some content slides including text content, image content, a combination of both, etc. A closing slide. we have included jpg files of our logo, let us know if you would prefer eps/vector. I assume you may want exact color data as well?

Target Market(s)

Technology and Customer Experience Leadership at companies with 25 or more employees

Industry/Entity Type

Technology Consulting

Font styles to use
Sans Serif

Colors
0054AA
0677BA
7BADD7
CADEEF
E8F1F8

Requirements
Must have
• I have attached JPG and EPS and vector files to project. I would like to stay with those colors but open to slight variation if recommended.

```html
<!DOCTYPE html>
<html lang="en">
<head>
<meta charset="utf-8">
<title>Norventa – Presentation Theme Overview</title>
<link href="https://fonts.googleapis.com/css2?family=Poppins:ital,wght@0,400;0,500;0,600;0,700;1,500&display=swap" rel="stylesheet">
<style>
:root{
  --primary:#0054AA;
  --accent:#0677BA;
  --soft:#7BADD7;
  --pale:#CADEEF;
  --mist:#E8F1F8;
  --ink:#1f1f24;
  --grey:#8d8d8f;
  --mute:#a3a3a6;
  --stage:#dcdde0;
  --white:#ffffff;
}
*{box-sizing:border-box;margin:0;padding:0}
html,body{width:1018px;height:1200px;overflow:hidden}
body{background:var(--stage);font-family:"Poppins",sans-serif;color:var(--ink)}
.canvas{position:relative;width:1018px;height:1200px}
.slide{position:absolute;width:307px;height:173px;background:var(--white);overflow:hidden}
.abs{position:absolute}
.title{position:absolute;left:11px;top:7px;font-weight:600;font-size:10.5px;line-height:1.2}
.rule{position:absolute;left:11px;top:23px;width:24px;height:1.6px;background:linear-gradient(to right,var(--primary) 0 66%,transparent 66% 74%,var(--soft) 74% 100%)}
.brand{position:absolute;right:7px;top:7px;font-weight:700;font-size:6px;letter-spacing:.3px}
.foot{position:absolute;left:10px;right:10px;bottom:7px;height:.6px;background:#2b2b30}
.page{position:absolute;right:6px;bottom:5px;font-size:3px;color:#2b2b30}
.tiny{font-size:3px;line-height:1.4;color:var(--mute)}
.small{font-size:4.6px;line-height:1.35;color:var(--grey)}
.head{font-weight:600;font-size:5px;color:var(--ink)}
.blue{color:var(--primary)}
.acc{color:var(--accent)}
.photo{position:absolute}
.dot{position:absolute;border-radius:50%}
.center{text-align:center}
</style>
</head>
<body>
<div class="canvas">

<!-- 1 Cover dark -->
<section class="slide" style="left:35px;top:40px">
  <div class="photo" role="img" aria-label="Black and white city skyline photo" style="inset:0;background:linear-gradient(160deg,#4a4a4e 0%,#2a2a2d 55%,#151517 100%)"></div>
  <div class="abs" style="left:7px;top:7px;width:6px;height:6px;background:#9a9a9e"></div>
  <div class="abs" style="left:24px;top:30px;font-weight:700;font-size:12px;color:var(--white);letter-spacing:.5px">NORVENTA</div>
  <div class="abs" style="left:24px;top:44px;width:91px;height:1px;background:#bdbdc0"></div>
  <div class="abs" style="left:25px;top:66px;font-weight:700;font-size:17px;line-height:1;color:var(--pale)">Business</div>
  <div class="abs" style="left:25px;top:83px;font-weight:700;font-size:21px;line-height:1;color:var(--soft)">Marketing</div>
  <div class="abs" style="left:25px;top:125px;font-style:italic;font-weight:500;font-size:7px;color:var(--soft)">Presentation</div>
  <div class="abs tiny" style="left:25px;top:136px;width:85px;color:#e4e4e6;font-style:italic">Lorem ipsum dolor sit amet, consectetuer adipiscing elit, sed diam nonum</div>
</section>

<!-- 2 Cover light -->
<section class="slide" style="left:355px;top:40px">
  <div class="abs" style="left:0;top:0;width:129px;height:173px;background:linear-gradient(135deg,#ffffff,var(--mist))"></div>
  <div class="abs" style="left:7px;top:7px;width:6px;height:6px;background:#111"></div>
  <div class="abs" style="left:22px;top:30px;font-weight:700;font-size:12px;letter-spacing:.5px">NORVENTA</div>
  <div class="abs" style="left:22px;top:44px;width:91px;height:1px;background:#b0b0b4"></div>
  <div class="abs" style="left:20px;top:66px;font-weight:500;font-size:8px;color:var(--primary)">Company</div>
  <div class="abs" style="left:20px;top:76px;font-weight:700;font-size:17px;line-height:1.1;color:#9b9b9f">Business</div>
  <div class="abs" style="left:20px;top:94px;font-weight:700;font-size:14.5px;line-height:1.1;color:var(--accent)">Marketing</div>
  <div class="abs" style="left:19px;top:123px;font-style:italic;font-weight:500;font-size:7px;color:var(--primary)">Presentation</div>
  <div class="abs tiny" style="left:19px;top:134px;width:92px;font-style:italic">Lorem ipsum dolor sit amet, consectetuer adipiscing elit, sed diam nonum</div>
  <div class="dot" style="left:19px;top:157px;width:3px;height:3px;background:#b8b8bb"></div>
  <div class="dot" style="left:25px;top:157px;width:3px;height:3px;background:var(--primary)"></div>
  <div class="dot" style="left:31px;top:157px;width:3px;height:3px;background:var(--soft)"></div>
  <div class="photo" role="img" aria-label="Photo of two colleagues working at a computer with holographic data" style="left:129px;top:0;width:178px;height:141px;background:linear-gradient(135deg,#1d2d4a 0%,#2f5d8e 45%,#14233d 100%)"></div>
  <div class="abs" style="left:129px;top:141px;width:178px;height:32px;background:var(--primary)"></div>
  <div class="abs" style="left:129px;top:152px;width:178px;text-align:center;font-size:5.5px;letter-spacing:2px;color:var(--white)">www.website.com</div>
</section>

<!-- 3 Agenda -->
<section class="slide" style="left:674px;top:40px">
  <div class="brand">NORVENTA</div>
  <div class="abs" style="left:82px;top:78px;font-weight:700;font-size:14px">Agenda</div>
  <div class="abs" style="left:157px;top:36px;width:120px"><div class="head blue" style="font-size:6px">1. Lorem ipsum</div><div class="tiny" style="padding-left:8px">Lorem ipsum dolor sit amet, consectetuer adipiscing elit, sed diam nonummy nibh euismod tincid</div></div>
  <div class="abs" style="left:157px;top:64px;width:120px"><div class="head acc" style="font-size:6px">2. Lorem ipsum</div><div class="tiny" style="padding-left:8px">Lorem ipsum dolor sit amet, consectetuer adipiscing elit, sed diam nonummy nibh euismod tincid</div></div>
  <div class="abs" style="left:157px;top:92px;width:120px"><div class="head blue" style="font-size:6px">3. Lorem ipsum</div><div class="tiny" style="padding-left:8px">Lorem ipsum dolor sit amet, consectetuer adipiscing elit, sed diam nonummy nibh euismod tincid</div></div>
  <div class="abs" style="left:157px;top:119px;width:120px"><div class="head acc" style="font-size:6px">4. Lorem ipsum</div><div class="tiny" style="padding-left:8px">Lorem ipsum dolor sit amet, consectetuer adipiscing elit, sed diam nonummy nibh euismod tincid</div></div>
  <div class="foot"></div><div class="page">2</div>
</section>

<!-- 4 List + panel -->
<section class="slide" style="left:35px;top:227px">
  <div class="title">Text Added Here</div><div class="rule"></div>
  <div class="brand">NORVENTA</div>
  <div class="abs" style="left:37px;top:43px;width:100px"><div class="head"><span style="margin-left:-10px;margin-right:3px">01.</span>Aliquam Erat Volutpat</div><div class="tiny">Lorem ipsum dolor sit amet, consectetuer adipiscing elit, sed diam nonummy nibh euismod</div></div>
  <div class="abs" style="left:37px;top:70px;width:100px"><div class="head"><span style="margin-left:-10px;margin-right:3px">02.</span>Consectetuer Adipiscing Elit</div><div class="tiny">Lorem ipsum dolor sit amet, consectetuer adipiscing elit, sed diam nonummy nibh euismod tincidunt ut laoreet</div></div>
  <div class="abs" style="left:37px;top:98px;width:100px"><div class="head"><span style="margin-left:-10px;margin-right:3px">03.</span>Duis Autem Vel Eum</div><div class="tiny">Lorem ipsum dolor sit amet, consectetuer adipiscing elit, sed diam nonummy nibh euismod tincidunt.</div></div>
  <div class="abs" style="left:37px;top:124px;width:100px"><div class="head"><span style="margin-left:-10px;margin-right:3px">04.</span>Aliquam Erat Volutpat</div><div class="tiny">Lorem ipsum dolor sit amet, consectetuer adipiscing elit, sed diam nonummy nibh euismod tincidunt ut laoreet.</div></div>
  <div class="abs" style="left:173px;top:42px;width:98px;height:102px;background:var(--primary)"></div>
  <svg class="abs" style="left:150px;top:46px" width="28" height="96" viewBox="0 0 28 96" aria-hidden="true">
    <g fill="var(--accent)" stroke="#fff" stroke-width="1.5"><circle cx="14" cy="13" r="11"/><circle cx="14" cy="44" r="11"/><circle cx="14" cy="77" r="11"/></g>
    <g fill="none" stroke="#fff" stroke-width="1.2"><circle cx="14" cy="13" r="5"/><path d="M9 46 h10 M14 40 v8"/><path d="M9 80 l3-4 3 3 4-5"/></g>
  </svg>
  <div class="abs" style="left:190px;top:52px;width:78px"><div style="font-weight:600;font-size:6px;color:#fff">Lorem ipsum</div><div class="tiny" style="color:var(--mist)">ipsum dolor sit amet, cons ectetuer adipiscing elit, sed diam nonummy nibh euismod tincidunt ut laoreet</div></div>
  <div class="abs" style="left:190px;top:83px;width:78px"><div style="font-weight:600;font-size:6px;color:#fff">Lorem ipsum</div><div class="tiny" style="color:var(--mist)">ipsum dolor sit amet, cons ectetuer adipiscing elit, sed diam nonummy nibh euismod tincidunt ut laoreet</div></div>
  <div class="abs" style="left:190px;top:116px;width:78px"><div style="font-weight:600;font-size:6px;color:#fff">Lorem ipsum</div><div class="tiny" style="color:var(--mist)">ipsum dolor sit amet, cons ectetuer adipiscing elit, sed diam nonummy nibh euismod tincidunt</div></div>
  <div class="foot"></div><div class="page">3</div>
</section>

<!-- 5 Three frames -->
<section class="slide" style="left:355px;top:227px">
  <div class="title">Text Added Here</div><div class="rule"></div>
  <div class="brand">NORVENTA</div>
  <svg class="abs" style="left:50px;top:41px" width="210" height="84" viewBox="0 0 210 84" aria-hidden="true">
    <g fill="none" stroke="#1f1f24" stroke-width="1.4">
      <path d="M8 2 h48 a4 4 0 0 1 4 4 v14 M56 80 h-48 a4 4 0 0 1 -4 -4 v-70 a4 4 0 0 1 4 -4"/>
      <path d="M60 20 v56 a4 4 0 0 1 -4 4"/>
      <path d="M78 2 h46 a4 4 0 0 1 4 4 v14 M74 60 v16 a4 4 0 0 0 4 4 h46 a4 4 0 0 0 4 -4 v-70 M74 60 v-54 a4 4 0 0 1 4 -4"/>
      <path d="M146 2 h48 a4 4 0 0 1 4 4 v70 a4 4 0 0 1 -4 4 h-48 a4 4 0 0 1 -4 -4 v-16 M142 60 v-54 a4 4 0 0 1 4 -4"/>
    </g>
    <g fill="#1f1f24"><circle cx="60" cy="20" r="2.6"/><circle cx="74" cy="60" r="2.6"/><circle cx="128" cy="20" r="2.6"/><circle cx="142" cy="60" r="2.6"/></g>
    <g fill="none" stroke="var(--primary)" stroke-width="1">
      <circle cx="32" cy="18" r="3.5"/><path d="M30.5 22 v3 h3 v-3"/>
      <rect x="95" y="15" width="10" height="7"/><path d="M95 15 l5 4 5 -4"/>
      <path d="M165 14 v9 h10 M166 21 l3-3 2 2 4-4"/>
    </g>
  </svg>
  <div class="abs acc" style="left:56px;top:70px;width:52px;text-align:center;font-weight:700;font-size:5px">IDEA</div>
  <div class="abs acc" style="left:124px;top:70px;width:56px;text-align:center;font-weight:700;font-size:5px">PROMOTION</div>
  <div class="abs acc" style="left:192px;top:70px;width:56px;text-align:center;font-weight:700;font-size:5px">GROWTH</div>
  <div class="abs tiny center" style="left:60px;top:78px;width:44px">Lorem ipsum dolor sit amet, consectetuer adipiscing elit, sed diam nonummy nibh euismod tincidunt ut laoreet dolore magna aliquam erat volutpat.</div>
  <div class="abs tiny center" style="left:128px;top:78px;width:48px">Lorem ipsum dolor sit amet, consectetuer adipiscing elit, sed diam nonummy nibh euismod tincidunt ut laoreet dolore magna aliquam erat volutpat.</div>
  <div class="abs tiny center" style="left:196px;top:78px;width:48px">Lorem ipsum dolor sit amet, consectetuer adipiscing elit, sed diam nonummy nibh euismod tincidunt ut laoreet dolore magna aliquam erat volutpat.</div>
  <div class="abs tiny center" style="left:36px;top:131px;width:235px;color:#666">Lorem ipsum dolor sit amet, consectetuer adipiscing elit, sed diam nonummy nibh euismod tincidunt ut laoreet dolore magna aliquam erat volutpat. Ut wisi enim ad minim veniam, quis nostrud exerci tation ullamcorper suscipit lobortis nisl ut aliquip ex ea commodo consequat.</div>
  <div class="foot"></div><div class="page">4</div>
</section>

<!-- 6 List + photos -->
<section class="slide" style="left:674px;top:227px">
  <div class="title">Text Added Here</div><div class="rule"></div>
  <div class="brand">NORVENTA</div>
  <div class="abs" style="left:23px;top:44px;width:125px"><div class="head" style="font-size:5.5px">1. Text Added Here</div><div class="tiny">Lorem ipsum dolor sit amet, cons ectetuer adipiscing elit, sed diam nonummy nibh euismod tincidunt ut laoreet dolore magna aliquam erat volutpat. Ut wisi enim ad minim veniam, quis nostrud exerci tation.</div></div>
  <div class="abs" style="left:23px;top:77px;width:125px"><div class="head" style="font-size:5.5px">2. Text Added Here</div><div class="tiny">Lorem ipsum dolor sit amet, cons ectetuer adipiscing elit, sed diam nonummy nibh euismod tincidunt ut laoreet dolore magna aliquam erat volutpat. Ut wisi enim ad minim veniam, quis nostrud exerci tation.</div></div>
  <div class="abs" style="left:23px;top:114px;width:125px"><div class="head" style="font-size:5.5px">3. Text Added Here</div><div class="tiny">Lorem ipsum dolor sit amet, cons ectetuer adipiscing elit, sed diam nonummy nibh euismod tincidunt ut laoreet dolore magna aliquam erat volutpat. Ut wisi enim ad minim veniam, quis nostrud exerci tation.</div></div>
  <div class="photo" role="img" aria-label="Photo of business people talking in a server room" style="left:158px;top:34px;width:72px;height:70px;background:linear-gradient(160deg,#2a4c78,#142640)"></div>
  <div class="photo" role="img" aria-label="Black and white photo of an office worker" style="left:212px;top:80px;width:72px;height:58px;background:linear-gradient(160deg,#a3a3a7,#5e5e62);border:2px solid #fff"></div>
  <div class="foot"></div><div class="page">5</div>
</section>

<!-- 7 Photo + items -->
<section class="slide" style="left:35px;top:415px">
  <div class="title">Text Added Here</div><div class="rule"></div>
  <div class="brand">NORVENTA</div>
  <div class="abs tiny" style="left:21px;top:38px;width:48px;font-size:3.4px;color:#888">Lorem ipsum dolor sit amet,consec-tetuer adipiscing elit, sed diam nonummy nibh euismod tincidunt erat volutpat.<br><br>Ut wisi enim ad minim veniam, quis nostrud exerci tation ullamcorper suscipit lobortis nisl ut aliquip ex ea commodo consequat.</div>
  <div class="photo" role="img" aria-label="Blue tinted photo of a man facing a digital interface wall" style="left:74px;top:23px;width:62px;height:90px;background:linear-gradient(160deg,var(--soft),var(--primary))"></div>
  <div class="photo" role="img" aria-label="Photo of a modern office interior" style="left:74px;top:115px;width:62px;height:36px;background:linear-gradient(160deg,var(--accent),#0a3f78)"></div>
  <svg class="abs" style="left:112px;top:33px" width="110" height="120" viewBox="0 0 110 120" aria-hidden="true">
    <g fill="#fff" stroke="var(--accent)" stroke-width="1.4"><circle cx="80" cy="15" r="11"/><circle cx="58" cy="55" r="11"/><circle cx="38" cy="96" r="11"/></g>
    <g fill="var(--primary)"><circle cx="80" cy="13" r="2"/><circle cx="76" cy="16" r="1.6"/><circle cx="84" cy="16" r="1.6"/><rect x="55" y="51" width="2" height="8"/><rect x="59" y="51" width="2" height="8"/><path d="M34 94 a2 2 0 0 1 4 -1 a2 2 0 0 1 4 1 l-4 4 z"/></g>
  </svg>
  <div class="abs" style="left:205px;top:40px;width:95px"><div class="head" style="font-size:6px;font-weight:700">We Before Me</div><div class="tiny">ipsum dolor sit amet, cons ectetuer adipiscing elit, sed diam nonummy nibh euismod tincidunt ut laoreet</div></div>
  <div class="abs" style="left:184px;top:80px;width:105px"><div class="head" style="font-size:6px;font-weight:700">We Are Good People</div><div class="tiny">ipsum dolor sit amet, cons ectetuer adipiscing elit, sed diam nonummy nibh euismod tincidunt ut laoreet dolore magna aliquam erat volutpat.</div></div>
  <div class="abs" style="left:164px;top:120px;width:110px"><div class="head" style="font-size:6px;font-weight:700">We Work with Heart</div><div class="tiny">ipsum dolor sit amet, cons ectetuer adipiscing elit, sed diam nonummy nibh euismod tincidunt</div></div>
  <div class="foot"></div><div class="page">6</div>
</section>

<!-- 8 Market chart -->
<section class="slide" style="left:355px;top:415px">
  <div class="brand">NORVENTA</div>
  <div class="abs" style="left:14px;top:14px;font-weight:600;font-size:10px;line-height:1.25">Market<br>Opportunities.</div>
  <div class="abs" style="left:14px;top:47px;width:24px;height:1.6px;background:linear-gradient(to right,var(--primary) 0 66%,transparent 66% 74%,var(--soft) 74%)"></div>
  <div class="abs" style="left:0;top:60px;width:107px;height:86px;background:var(--mist)"></div>
  <div class="abs" style="left:14px;top:65px;width:86px;font-size:4.4px;line-height:1.35;color:#8d8d8f">Lorem ipsum dolor sit amet, consectetuer adipiscing elit, sed diam nonummy nibh euismod tincidunt ut laoreet dolore magna aliquam erat volutpat. Ut wisi enim ad minim veniam, quis nostrud exerci tation ullamcorper suscipit lobortis nisl ut aliquip ex ea commodo consequat. Duis autem vel eum iriure dolor in hendrerit i</div>
  <div class="abs" style="left:127px;top:19px;font-size:4.6px;color:#444;letter-spacing:.2px">CONSECTETUER ADIPISCING</div>
  <svg class="abs" style="left:125px;top:30px" width="170" height="90" viewBox="0 0 170 90" font-family="Poppins, sans-serif" font-size="4.6" fill="#333">
    <g stroke="#cfcfd2" stroke-width=".5">
      <line x1="15" y1="5" x2="165" y2="5"/><line x1="15" y1="16.7" x2="165" y2="16.7"/><line x1="15" y1="28.3" x2="165" y2="28.3"/><line x1="15" y1="40" x2="165" y2="40"/><line x1="15" y1="51.7" x2="165" y2="51.7"/><line x1="15" y1="63.3" x2="165" y2="63.3"/><line x1="15" y1="75" x2="165" y2="75"/><line x1="165" y1="5" x2="165" y2="75"/>
    </g>
    <text x="8" y="7">60</text><text x="8" y="18.5">50</text><text x="8" y="30">40</text><text x="8" y="42">30</text><text x="8" y="53.5">20</text><text x="8" y="65">10</text><text x="10" y="77">0</text>
    <rect x="31" y="10.8" width="17" height="64.2" fill="var(--primary)"/>
    <rect x="64" y="37.7" width="17" height="37.3" fill="var(--soft)"/>
    <rect x="96" y="19" width="17" height="56" fill="var(--primary)"/>
    <rect x="128" y="42.3" width="17" height="32.7" fill="var(--soft)"/>
    <text x="34" y="84">JAN</text><text x="67" y="84">FEB</text><text x="99" y="84">MAR</text><text x="131" y="84">APR</text>
  </svg>
  <div class="dot" style="left:125px;top:127px;width:4px;height:4px;background:var(--primary)"></div>
  <div class="abs" style="left:133px;top:124px;width:70px"><div style="font-size:5.5px;font-weight:500;color:var(--accent)">Lorem Ipsum</div><div class="tiny">Lorem ipsum dolor sit amet, consectetuer adipiscing elit, sed diam nonummy nibh euismod tincidunt ut laoreet</div></div>
  <div class="dot" style="left:210px;top:127px;width:4px;height:4px;background:var(--soft)"></div>
  <div class="abs" style="left:218px;top:124px;width:70px"><div style="font-size:5.5px;font-weight:500;color:var(--accent)">Lorem Ipsum</div><div class="tiny">Lorem ipsum dolor sit amet, consectetuer adipiscing elit, sed diam nonummy nibh euismod tincidunt ut laoreet</div></div>
  <div class="foot"></div><div class="page">7</div>
</section>

<!-- 9 Photo + cards -->
<section class="slide" style="left:674px;top:415px">
  <div class="brand">NORVENTA</div>
  <div class="abs" style="left:16px;top:11px;font-weight:600;font-size:10px;line-height:1.3">Lorem Ipsum<br>Dolor Sit<br>Ametkeeper.</div>
  <div class="abs" style="left:16px;top:57px;width:24px;height:1.6px;background:linear-gradient(to right,var(--primary) 0 66%,transparent 66% 74%,var(--soft) 74%)"></div>
  <div class="abs tiny" style="left:16px;top:64px;width:77px;text-align:justify;font-size:3.3px">Lorem ipsum dolor sit amet, consectetuer adipiscing elit, sed diam nonummy nibh euismod tincidunt ut laoreet dolore magna aliquam erat volutpat.<br><br>Ut wisi enim ad minim veniam, quis nostrud exerci tation ullamcorper suscipit lobortis nisl ut aliquip ex ea commodo consequat. Duis autem vel eum iriure dolor in hendrerit in vulputate velit esse molestie consequat.<br><br>vel illum dolore eu feugiat nulla facilisis at vero eros et accumsan et iusto odio</div>
  <div class="photo" role="img" aria-label="Photo of hands using a tablet with glowing data graphics" style="left:107px;top:28px;width:200px;height:81px;background:linear-gradient(120deg,#1e3558 0%,var(--accent) 55%,#0c2645 100%)"></div>
  <div class="abs" style="left:134px;top:88px;width:54px;height:14px;background:var(--primary);color:#fff;font-weight:600;font-size:7.5px;text-align:center;line-height:14px">Text Here</div>
  <div class="abs" style="left:208px;top:88px;width:54px;height:14px;background:var(--accent);color:#fff;font-weight:600;font-size:7.5px;text-align:center;line-height:14px">Text Here</div>
  <div class="abs tiny" style="left:136px;top:102px;width:50px;height:50px;background:#fff;padding:2px 3px;box-shadow:0 0 2px rgba(0,0,0,.18)">Lorem ipsum dolor sit amet, consectetuer adipiscing elit, sed diam nonummy nibh euismod tincidunt ut laoreet dolore magna aliquam erat volutpat.<br><br>Ut wisi enim ad minim veniam, quis nostrud exerci tation</div>
  <div class="abs tiny" style="left:210px;top:102px;width:50px;height:50px;background:#fff;padding:2px 3px;box-shadow:0 0 2px rgba(0,0,0,.18)">Lorem ipsum dolor sit amet, consectetuer adipiscing elit, sed diam nonummy nibh euismod tincidunt ut laoreet dolore magna aliquam erat volutpat.<br><br>Ut wisi enim ad minim veniam, quis nostrud exerci tation</div>
  <div class="foot"></div><div class="page">8</div>
</section>

<!-- 10 Three options -->
<section class="slide" style="left:35px;top:605px">
  <div class="title">Text Added Here</div><div class="rule"></div>
  <div class="brand">NORVENTA</div>
  <svg class="abs" style="left:25px;top:78px" width="35" height="36" viewBox="0 0 35 36" aria-hidden="true"><polygon points="0,0 16,0 34,18 16,36 0,36 18,18" fill="var(--mist)"/></svg>
  <div class="photo" role="img" aria-label="Photo of a digital security padlock interface" style="left:79px;top:38px;width:58px;height:69px;background:linear-gradient(160deg,#5f7fa8,#23395a)"></div>
  <div class="photo" role="img" aria-label="Photo of two businessmen reviewing a laptop" style="left:154px;top:38px;width:58px;height:69px;background:linear-gradient(160deg,#5a5a5d,#1f1f22)"></div>
  <div class="photo" role="img" aria-label="Photo of a team working with holographic screens" style="left:229px;top:38px;width:58px;height:69px;background:linear-gradient(160deg,#3f6a9a,#15294a)"></div>
  <div class="abs" style="left:79px;top:112px;width:60px"><div style="font-size:5px;font-weight:500"><span class="blue">First</span> <span class="acc">Option</span></div><div class="tiny">Lorem ipsum dolor sit consectetuer adipiscing elit, sed diam nonummy nibh euismod tincidunt ut dolore magna aliquam erat volutpat. Ut wisi enim ad minim veniam, quis nostrud</div></div>
  <div class="abs" style="left:154px;top:112px;width:60px"><div style="font-size:5px;font-weight:500"><span class="blue">Second</span> <span class="acc">Option</span></div><div class="tiny">Lorem ipsum dolor sit consectetuer adipiscing elit, sed diam nonummy nibh euismod tincidunt ut dolore magna aliquam erat volutpat. Ut wisi enim ad minim veniam, quis nostrud</div></div>
  <div class="abs" style="left:229px;top:112px;width:60px"><div style="font-size:5px;font-weight:500"><span class="blue">Third</span> <span class="acc">Option</span></div><div class="tiny">Lorem ipsum dolor sit consectetuer adipiscing elit, sed diam nonummy nibh euismod tincidunt ut dolore magna aliquam erat volutpat. Ut wisi enim ad minim veniam, quis nostrud</div></div>
  <div class="foot"></div><div class="page">9</div>
</section>

<!-- 11 Four framed boxes -->
<section class="slide" style="left:355px;top:605px">
  <div class="title">Text Added Here</div><div class="rule"></div>
  <div class="brand">NORVENTA</div>
  <svg class="abs" style="left:40px;top:40px" width="235" height="100" viewBox="0 0 235 100" aria-hidden="true">
    <g fill="none" stroke="#1f1f24" stroke-width="1">
      <path d="M5 10 v85 h43 v-85 M5 10 h8 M48 10 h-8"/>
      <path d="M63 10 v85 h43 v-85 M63 10 h8 M106 10 h-8"/>
      <path d="M121 10 v85 h43 v-85 M121 10 h8 M164 10 h-8"/>
      <path d="M179 10 v85 h43 v-85 M179 10 h8 M222 10 h-8"/>
    </g>
    <circle cx="26.5" cy="10" r="8.5" fill="var(--primary)"/><circle cx="84.5" cy="10" r="8.5" fill="var(--accent)"/><circle cx="142.5" cy="10" r="8.5" fill="var(--primary)"/><circle cx="200.5" cy="10" r="8.5" fill="var(--accent)"/>
    <g fill="none" stroke="#fff" stroke-width=".9"><rect x="23" y="7" width="7" height="6"/><rect x="81" y="7" width="7" height="5"/><path d="M138.5 10 l4 -2 4 2 -4 2 z M140 11 v2 h5 v-2"/><rect x="197" y="7" width="7" height="6"/></g>
  </svg>
  <div class="abs" style="left:51px;top:62px;width:38px"><div style="font-size:4.6px;font-weight:600" class="acc">Lorem ipsum</div><div class="tiny">ipsum dolor sit amet, cons ectetuer adipiscing elit, sed diam nonummy nibh euismod tincidunt ut laoreet<br><br>ipsum dolor sit amet, cons ectetuer adipiscing elit, sed diam nonummy nibh euismod tincidunt ut laoreet</div></div>
  <div class="abs" style="left:109px;top:62px;width:38px"><div style="font-size:4.6px;font-weight:600" class="blue">Lorem ipsum</div><div class="tiny">ipsum dolor sit amet, cons ectetuer adipiscing elit, sed diam nonummy nibh euismod tincidunt ut laoreet<br><br>ipsum dolor sit amet, cons ectetuer adipiscing elit, sed diam nonummy nibh euismod tincidunt ut laoreet</div></div>
  <div class="abs" style="left:167px;top:62px;width:38px"><div style="font-size:4.6px;font-weight:600" class="acc">Lorem ipsum</div><div class="tiny">ipsum dolor sit amet, cons ectetuer adipiscing elit, sed diam nonummy nibh euismod tincidunt ut laoreet<br><br>ipsum dolor sit amet, cons ectetuer adipiscing elit, sed diam nonummy nibh euismod tincidunt ut laoreet</div></div>
  <div class="abs" style="left:225px;top:62px;width:38px"><div style="font-size:4.6px;font-weight:600" class="blue">Lorem ipsum</div><div class="tiny">ipsum dolor sit amet, cons ectetuer adipiscing elit, sed diam nonummy nibh euismod tincidunt ut laoreet<br><br>ipsum dolor sit amet, cons ectetuer adipiscing elit, sed diam nonummy nibh euismod tincidunt ut laoreet</div></div>
  <div class="abs" style="left:45px;top:138px;font-weight:700;font-size:9px">+ 35k</div>
  <div class="abs tiny" style="left:45px;top:151px;width:180px;color:#666">Lorem ipsum dolor sit amet, consectetuer adipiscing elit, sed diam nonummy nibh euismod tincidunt ut laoreet dolore magna aliquam erat volutpat. Ut wisi enim ad minim veniam, quis nostrud exerci tation ullamcorper</div>
  <div class="foot"></div><div class="page">10</div>
</section>

<!-- 12 Ring + project list -->
<section class="slide" style="left:674px;top:605px">
  <div class="title">Text Added Here</div><div class="rule"></div>
  <div class="brand">NORVENTA</div>
  <svg class="abs" style="left:30px;top:40px" width="180" height="100" viewBox="0 0 180 100" aria-hidden="true">
    <circle cx="40" cy="49" r="35" fill="none" stroke="#111" stroke-width="3.5"/>
    <circle cx="40" cy="49" r="30" fill="none" stroke="#111" stroke-width=".8"/>
    <path d="M78 25 l15 -20 h38 M78 49 h53 M78 73 l15 20 h38" fill="none" stroke="#111" stroke-width=".7"/>
  </svg>
  <div class="abs center" style="left:40px;top:85px;width:60px;font-weight:700;font-size:7px">NORVENTA</div>
  <svg class="abs" style="left:152px;top:26px" width="30" height="110" viewBox="0 0 30 110" aria-hidden="true">
    <g fill="var(--primary)"><circle cx="15" cy="15" r="12"/><circle cx="15" cy="54" r="12"/><circle cx="15" cy="94" r="12"/></g>
    <g fill="none" stroke="#fff" stroke-width=".9"><circle cx="15" cy="15" r="5"/><circle cx="15" cy="15" r="2"/><circle cx="15" cy="54" r="5"/><circle cx="15" cy="54" r="2"/><circle cx="15" cy="94" r="5"/><circle cx="15" cy="94" r="2"/></g>
  </svg>
  <div class="abs" style="left:185px;top:33px;width:100px"><div style="font-size:6.5px;font-weight:500" class="acc">Project name</div><div class="tiny" style="color:#666">Lorem ipsum dolor sit amet, nec an dictas equidem appellantur, ut has commune accommodare. Mea illum, ludus solet idpro.</div></div>
  <div class="abs" style="left:185px;top:72px;width:100px"><div style="font-size:6.5px;font-weight:500" class="acc">Project name</div><div class="tiny" style="color:#666">Lorem ipsum dolor sit amet, nec an dictas equidem appellantur, ut has commune accommodare. Mea illum, ludus solet idpro.</div></div>
  <div class="abs" style="left:185px;top:112px;width:100px"><div style="font-size:6.5px;font-weight:500" class="acc">Project name</div><div class="tiny" style="color:#666">Lorem ipsum dolor sit amet, nec an dictas equidem appellantur, ut has commune accommodare. Mea illum, ludus solet idpro.</div></div>
  <div class="foot"></div><div class="page">11</div>
</section>

<!-- 13 Timeline -->
<section class="slide" style="left:35px;top:797px">
  <div class="title">Text Added Here</div><div class="rule"></div>
  <div class="brand">NORVENTA</div>
  <div class="abs center" style="left:25px;top:47px;width:60px"><div class="head">Your Title</div><div class="small" style="font-size:3.8px">Refers to a good or service being offered</div></div>
  <div class="abs center" style="left:125px;top:47px;width:60px"><div class="head">Your Title</div><div class="small" style="font-size:3.8px">Refers to a good or service being offered</div></div>
  <div class="abs center" style="left:225px;top:47px;width:60px"><div class="head">Your Title</div><div class="small" style="font-size:3.8px">Refers to a good or service being offered</div></div>
  <div class="abs center" style="left:75px;top:124px;width:60px"><div class="head">Your Title</div><div class="small" style="font-size:3.8px">Refers to a good or service being offered</div></div>
  <div class="abs center" style="left:175px;top:124px;width:60px"><div class="head">Your Title</div><div class="small" style="font-size:3.8px">Refers to a good or service being offered</div></div>
  <svg class="abs" style="left:25px;top:64px" width="260" height="60" viewBox="0 0 260 60" font-family="Poppins, sans-serif" font-size="4.4" fill="#fff">
    <g stroke="var(--primary)" stroke-width=".8"><line x1="30" y1="4" x2="30" y2="20"/><line x1="130" y1="4" x2="130" y2="20"/><line x1="230" y1="4" x2="230" y2="20"/></g>
    <g fill="var(--primary)"><circle cx="30" cy="7" r="2.2"/><circle cx="130" cy="7" r="2.2"/><circle cx="230" cy="7" r="2.2"/></g>
    <g stroke="var(--accent)" stroke-width=".8"><line x1="80" y1="36" x2="80" y2="52"/><line x1="180" y1="36" x2="180" y2="52"/></g>
    <g fill="var(--accent)"><circle cx="80" cy="50" r="2.2"/><circle cx="180" cy="50" r="2.2"/></g>
    <polygon points="8,27 52,27 48,35 0,35" fill="var(--primary)"/>
    <polygon points="54,27 102,27 106,35 50,35" fill="var(--accent)"/>
    <polygon points="104,27 156,27 152,35 108,35" fill="var(--primary)"/>
    <polygon points="158,27 202,27 206,35 154,35" fill="var(--accent)"/>
    <polygon points="204,27 252,27 260,35 208,35" fill="var(--primary)"/>
    <text x="23" y="33">1990</text><text x="73" y="33">2001</text><text x="123" y="33">2007</text><text x="173" y="33">2012</text><text x="223" y="33">2020</text>
  </svg>
  <div class="foot"></div><div class="page">12</div>
</section>

<!-- 14 Circular segments -->
<section class="slide" style="left:355px;top:797px">
  <div class="title">Text Added Here</div><div class="rule"></div>
  <div class="brand">NORVENTA</div>
  <svg class="abs" style="left:110px;top:50px" width="90" height="90" viewBox="0 0 90 90" font-family="Poppins, sans-serif">
    <circle cx="45" cy="45" r="33" fill="none" stroke="var(--accent)" stroke-width="19"/>
    <circle cx="45" cy="45" r="33" fill="none" stroke="var(--primary)" stroke-width="19" stroke-dasharray="51.8 51.8"/>
    <g stroke="#fff" stroke-width="1.4"><line x1="45" y1="2" x2="45" y2="24"/><line x1="45" y1="66" x2="45" y2="88"/><line x1="2" y1="45" x2="24" y2="45"/><line x1="66" y1="45" x2="88" y2="45"/></g>
    <g fill="#fff"><circle cx="45" cy="13" r="3"/><circle cx="77" cy="45" r="3"/><circle cx="45" cy="77" r="3"/><circle cx="13" cy="45" r="3"/></g>
    <circle cx="45" cy="45" r="22" fill="#fff"/>
    <g fill="none" stroke="#fff" stroke-width=".9"><circle cx="22" cy="22" r="4"/><path d="M64 18 l6 -3 -3 6 z"/><rect x="17" y="63" width="7" height="6"/><circle cx="68" cy="68" r="4"/></g>
    <text x="45" y="43" text-anchor="middle" font-weight="700" font-size="7.5" fill="#1f1f24">Text</text>
    <text x="45" y="52" text-anchor="middle" font-weight="700" font-size="7.5" fill="#1f1f24">Added</text>
  </svg>
  <div class="abs" style="left:30px;top:43px;width:73px;text-align:right"><div class="head" style="font-size:5.5px">Text Here</div><div class="tiny" style="color:#777">Lorem ipsum dolor sit amet, consectetuer adipiscing elit, sed diammy nibh euismod tincidunt ut laoreet dolore</div></div>
  <div class="abs" style="left:30px;top:104px;width:73px;text-align:right"><div class="head" style="font-size:5.5px">Text Here</div><div class="tiny" style="color:#777">Lorem ipsum dolor sit amet, consectetuer adipiscing elit, sed diammy nibh euismod tincidunt ut laoreet dolore</div></div>
  <div class="abs" style="left:206px;top:43px;width:73px"><div class="head" style="font-size:5.5px">Text Here</div><div class="tiny" style="color:#777">Lorem ipsum dolor sit amet, consectetuer adipiscing elit, sed diammy nibh euismod tincidunt ut laoreet dolore</div></div>
  <div class="abs" style="left:206px;top:104px;width:73px"><div class="head" style="font-size:5.5px">Text Here</div><div class="tiny" style="color:#777">Lorem ipsum dolor sit amet, consectetuer adipiscing elit, sed diammy nibh euismod tincidunt ut laoreet dolore</div></div>
  <div class="foot"></div><div class="page">13</div>
</section>

<!-- 15 Steps -->
<section class="slide" style="left:674px;top:797px">
  <div class="title">Text Added Here</div><div class="rule"></div>
  <div class="brand">NORVENTA</div>
  <svg class="abs" style="left:38px;top:58px" width="240" height="28" viewBox="0 0 240 28" font-family="Poppins, sans-serif" font-size="5" font-weight="600" fill="#fff">
    <polygon points="0,1 42,1 54,14 42,27 0,27 10,14" fill="var(--primary)"/>
    <polygon points="46,1 88,1 100,14 88,27 46,27 56,14" fill="var(--accent)"/>
    <polygon points="92,1 134,1 146,14 134,27 92,27 102,14" fill="var(--primary)"/>
    <polygon points="138,1 180,1 192,14 180,27 138,27 148,14" fill="var(--accent)"/>
    <polygon points="184,1 226,1 238,14 226,27 184,27 194,14" fill="var(--primary)"/>
    <text x="16" y="16">STEP 01</text><text x="62" y="16">STEP 02</text><text x="108" y="16">STEP 03</text><text x="154" y="16">STEP 04</text><text x="200" y="16">STEP 05</text>
  </svg>
  <div class="abs center" style="left:37px;top:94px;width:44px"><div class="head">Project name</div><div class="tiny" style="color:#777">Lorem Ipsum is simply dummy unknown printer took a galley of type and scrambled it to make.</div></div>
  <div class="abs center" style="left:83px;top:94px;width:44px"><div class="head">Project name</div><div class="tiny" style="color:#777">Lorem Ipsum is simply dummy unknown printer took a galley of type and scrambled it to make.</div></div>
  <div class="abs center" style="left:129px;top:94px;width:44px"><div class="head">Project name</div><div class="tiny" style="color:#777">Lorem Ipsum is simply dummy unknown printer took a galley of type and scrambled it to make.</div></div>
  <div class="abs center" style="left:175px;top:94px;width:44px"><div class="head">Project name</div><div class="tiny" style="color:#777">Lorem Ipsum is simply dummy unknown printer took a galley of type and scrambled it to make.</div></div>
  <div class="abs center" style="left:221px;top:94px;width:44px"><div class="head">Project name</div><div class="tiny" style="color:#777">Lorem Ipsum is simply dummy unknown printer took a galley of type and scrambled it to make.</div></div>
  <div class="foot"></div><div class="page">14</div>
</section>

<!-- 16 Phones -->
<section class="slide" style="left:35px;top:987px">
  <div class="title">Text Added Here</div><div class="rule"></div>
  <div class="brand">NORVENTA</div>
  <div class="abs tiny" style="left:13px;top:33px;width:96px;font-size:3.3px;color:#777">Lorem ipsum dolor sit amet, consectetuer adipiscing elit, sed diam nonummy nibh euismod tincidunt ut laoreet dolore magna aliquam erat volutpat. Ut wisi enim ad minim veniam,<br><br>quis nostrud exerci tation ullamcorper suscipit lobortis nisl ut aliquip ex ea commodo consequat. Duis autem vel eum iriure dolor in hendrerit in vulputate velit esse</div>
  <div class="abs" style="left:23px;top:87px;width:9px;height:9px;background:var(--primary);color:#fff;font-size:5.5px;font-weight:600;text-align:center;line-height:9px">1.</div>
  <div class="abs" style="left:36px;top:87px;width:75px"><div style="font-size:4.5px;font-weight:500" class="acc">Lorem ipsum</div><div class="tiny" style="color:#777">Lorem ipsum dolor sit amet, consectetuer adipiscing elit, sed diam nonummy nibh euismod tincid</div></div>
  <div class="abs" style="left:23px;top:109px;width:9px;height:9px;background:var(--primary);color:#fff;font-size:5.5px;font-weight:600;text-align:center;line-height:9px">2.</div>
  <div class="abs" style="left:36px;top:109px;width:75px"><div style="font-size:4.5px;font-weight:500" class="acc">Lorem ipsum</div><div class="tiny" style="color:#777">Lorem ipsum dolor sit amet, consectetuer adipiscing elit, sed diam nonummy nibh euismod tincid</div></div>
  <div class="abs" style="left:23px;top:130px;width:9px;height:9px;background:var(--primary);color:#fff;font-size:5.5px;font-weight:600;text-align:center;line-height:9px">3.</div>
  <div class="abs" style="left:36px;top:130px;width:75px"><div style="font-size:4.5px;font-weight:500" class="acc">Lorem ipsum</div><div class="tiny" style="color:#777">Lorem ipsum dolor sit amet, consectetuer adipiscing elit, sed diam nonummy nibh euismod tincid</div></div>
  <div class="abs" style="left:128px;top:20px;width:160px;height:130px;background:var(--mist)"></div>
  <div class="abs" style="left:138px;top:24px;width:36px;height:77px;border:1.6px solid #1f1f24;border-radius:4px;background:#fff;padding:10px 3px 0">
    <div style="font-size:4.5px;line-height:1.25">Lorem ipsum dolor</div>
    <div class="tiny" style="font-size:2.2px;margin-top:12px;color:#777">To introduce the students to the changing landscape of marketing and equip them with knowledge and tools to navigate the digital marketing world.</div>
  </div>
  <div class="abs" style="left:184px;top:50px;width:36px;height:77px;border:1.6px solid #1f1f24;border-radius:4px;background:#fff;padding:14px 3px 0">
    <div style="font-size:4.5px;line-height:1.25">Dolor sit amet, conse</div>
    <div class="dot" style="left:15px;top:30px;width:5px;height:5px;border:.7px solid var(--accent)"></div>
    <div class="tiny" style="font-size:2.2px;margin-top:14px;color:#777">You will learn concepts and ideas in digital marketing as well as how to use different tools and strategies to optimize your digital marketing campaigns.</div>
  </div>
  <div class="abs" style="left:229px;top:74px;width:36px;height:77px;border:1.6px solid #1f1f24;border-radius:4px;background:#fff;padding:16px 3px 0">
    <div style="font-size:4.5px;line-height:1.25">Consec</div>
    <div style="font-size:4px;color:#999;letter-spacing:.8px">· · · · · ·</div>
    <div class="dot" style="left:15px;top:32px;width:5px;height:5px;border:.7px solid var(--accent)"></div>
    <div class="tiny" style="font-size:2.2px;margin-top:14px;color:#777">You are required to pass 80% of the evaluation test to obtain the certificate. The evaluation test can only be taken 3 times.</div>
  </div>
  <div class="foot"></div><div class="page">15</div>
</section>

<!-- 17 Team -->
<section class="slide" style="left:355px;top:987px">
  <div class="title">Text Added Here</div><div class="rule"></div>
  <div class="brand">NORVENTA</div>
  <div class="abs" style="left:28px;top:55px;width:46px;height:20px;background:var(--primary)"></div>
  <div class="abs" style="left:96px;top:55px;width:46px;height:20px;background:var(--accent)"></div>
  <div class="abs" style="left:165px;top:55px;width:46px;height:20px;background:var(--primary)"></div>
  <div class="abs" style="left:235px;top:55px;width:46px;height:20px;background:var(--accent)"></div>
  <div class="dot" role="img" aria-label="Portrait photo of a team member" style="left:39px;top:62px;width:24px;height:24px;border:1.5px solid #fff;background:linear-gradient(var(--pale),#8e8e92)"></div>
  <div class="dot" role="img" aria-label="Portrait photo of a team member" style="left:107px;top:62px;width:24px;height:24px;border:1.5px solid #fff;background:linear-gradient(var(--pale),#8e8e92)"></div>
  <div class="dot" role="img" aria-label="Portrait photo of a team member" style="left:176px;top:62px;width:24px;height:24px;border:1.5px solid #fff;background:linear-gradient(var(--pale),#8e8e92)"></div>
  <div class="dot" role="img" aria-label="Portrait photo of a team member" style="left:246px;top:62px;width:24px;height:24px;border:1.5px solid #fff;background:linear-gradient(var(--pale),#8e8e92)"></div>
  <div class="abs center" style="left:20px;top:90px;width:62px"><div class="head" style="font-size:5.5px;font-weight:700">JOHN SMITH</div><div class="tiny" style="color:#777">ipsum dolor sit amet, cons ectetuer adipiscing elit, sed diam nonummy nibh euismod tincidunt<br><br>ut laoreet dolore magna aliquam erat volutpat. Ut wisi enim ad minim veniam, quis nostrud</div></div>
  <div class="abs center" style="left:88px;top:90px;width:62px"><div class="head" style="font-size:5.5px;font-weight:700">MILLIE SMITH</div><div class="tiny" style="color:#777">ipsum dolor sit amet, cons ectetuer adipiscing elit, sed diam nonummy nibh euismod tincidunt<br><br>aliquam erat volutpat. Ut wisi enim ad minim veniam, quis nostrud</div></div>
  <div class="abs center" style="left:157px;top:90px;width:62px"><div class="head" style="font-size:5.5px;font-weight:700">JOHN SMITH</div><div class="tiny" style="color:#777">ipsum dolor sit amet, cons ectetuer adipiscing elit, sed diam nonummy nibh euismod tincidunt<br><br>Ut wisi enim ad minim veniam, quis nostrud</div></div>
  <div class="abs center" style="left:227px;top:90px;width:62px"><div class="head" style="font-size:5.5px;font-weight:700">MILLIE SMITH</div><div class="tiny" style="color:#777">ipsum dolor sit amet, cons ectetuer adipiscing elit, sed diam nonummy nibh euismod tincidunt<br><br>aliquam erat volutpat. Ut wisi enim ad minim veniam, quis nostrud</div></div>
  <div class="foot"></div><div class="page">15</div>
</section>

<!-- 18 Thank you -->
<section class="slide" style="left:674px;top:987px">
  <div class="abs" style="left:0;top:0;width:34px;height:104px;background:var(--primary)"></div>
  <div class="abs" style="left:0;top:104px;width:34px;height:69px;background:var(--accent)"></div>
  <div class="abs center" style="left:60px;top:114px;width:90px;font-weight:700;font-size:10px;letter-spacing:.6px">NORVENTA</div>
  <div class="abs" style="left:152px;top:44px;font-weight:700;font-size:19px;line-height:1.1">Thank <span class="acc">You</span></div>
  <svg class="abs" style="left:152px;top:78px" width="12" height="70" viewBox="0 0 12 70" aria-hidden="true">
    <path d="M2 3 c0 5 4 9 8 9 l1-3 -3-1 -1 1.5 c-1.5-.5-3-2-3.5-3.5 l1.5-1 -1-3 z" fill="var(--primary)"/>
    <path d="M2 27 l9 -4 -3 9 -1.5 -3.5 z" fill="var(--primary)"/>
    <path d="M6 48 l-5 4.5 h1.5 v4.5 h2.5 v-3 h2 v3 h2.5 v-4.5 h1.5 z" fill="var(--primary)"/>
  </svg>
  <div class="abs" style="left:167px;top:78px;height:16px;width:.6px;background:#777"></div>
  <div class="abs" style="left:167px;top:99px;height:10px;width:.6px;background:#777"></div>
  <div class="abs" style="left:167px;top:117px;height:16px;width:.6px;background:#777"></div>
  <div class="abs small" style="left:173px;top:78px;font-size:4.8px;color:#666">+18 2767 5500 2140<br>+18 2767 5500 2140</div>
  <div class="abs small" style="left:173px;top:98px;font-size:4.8px;color:#666">www.norventa-demo.com<br>hello@norventa-demo.com</div>
  <div class="abs small" style="left:173px;top:117px;font-size:4.8px;color:#666">1234 Street name, town/city,<br>state/country, post/zip 012345.</div>
</section>

</div>
</body>
</html>
```